New LLC consulting company needs a business card design

I need a business card design for new company in Alexandria Virginia called TK Verdane Consulting LLC. The company is focused on consulting for defense and national security issues with expertise in nuclear and space topics. I would like to see designs that are simple and I am open to colors except for brown.

Target Market(s)

All businesses that are seeking consulting help

Industry/Entity Type

Consulting

Contact Information for Business Card

Name of company - TK Verdane Consulting LLC; name (Delia Pratt) President; email: prattdq47@mailvessa.com; Phone: 703-555-0142

Requirements
Must have
• The details described above
Nice to have
• I'm open to all ideas
Should not have
• No brown

```html
<!DOCTYPE html>
<html lang="en">
<head>
<meta charset="utf-8">
<title>TK Verdane Consulting LLC — Business Card</title>
<link rel="stylesheet" href="https://fonts.googleapis.com/css2?family=Poppins:wght@400;500;600;700&display=swap">
<style>
  :root {
    --backdrop: #f1f1f1;
    --brand-blue: #1177be;
    --card-dark: #1e1e1e;
    --white: #ffffff;
  }
  * { box-sizing: border-box; margin: 0; padding: 0; }
  html, body {
    width: 1200px; height: 987px; overflow: hidden;
    background: var(--backdrop);
    font-family: "Poppins", sans-serif;
  }
  .card {
    position: absolute;
    left: 245px;
    width: 709px;
    height: 405px;
    overflow: hidden;
  }
  .card--front { top: 68px; background: var(--brand-blue); }
  .card--back { top: 514px; background: var(--card-dark); }

  .wordmark {
    position: absolute;
    left: 0; right: 0;
    text-align: center;
    color: var(--white);
    font-weight: 700;
    line-height: 1;
  }
  .wordmark__name { display: block; font-size: 56px; letter-spacing: 1px; }
  .wordmark__tag { display: block; font-size: 22px; letter-spacing: 11px; margin-top: 12px; padding-left: 11px; }
  .card--front .wordmark { top: 152px; }
  .card--back .wordmark { top: 58px; }
  .card--back .wordmark__name { font-size: 50px; }
  .card--back .wordmark__tag { font-size: 19px; letter-spacing: 10px; margin-top: 10px; }

  .wave { position: absolute; left: 0; top: 0; width: 709px; height: 405px; }
  .wave__base { fill: var(--brand-blue); }
  .wave__swoosh { fill: var(--white); }

  .person {
    position: absolute;
    right: 396px;
    top: 260px;
    text-align: right;
    color: var(--white);
  }
  .person__name { font-size: 35px; font-weight: 400; line-height: 1.1; white-space: nowrap; }
  .person__first { color: var(--brand-blue); font-weight: 600; }
  .person__role { font-size: 17px; font-weight: 500; letter-spacing: 0.5px; margin-top: 2px; }

  .divider {
    position: absolute;
    left: 354px; top: 243px;
    width: 2px; height: 105px;
    background: var(--brand-blue);
  }

  .contact {
    position: absolute;
    left: 390px; top: 266px;
    list-style: none;
    color: var(--white);
    font-size: 18px;
    letter-spacing: 0.6px;
  }
  .contact__item { display: flex; align-items: center; height: 24px; margin-bottom: 1px; }
  .contact__icon { width: 16px; height: 16px; margin-right: 12px; flex: none; }
  .contact__icon path, .contact__icon rect { fill: none; stroke: var(--brand-blue); stroke-width: 1.8; stroke-linecap: round; stroke-linejoin: round; }
</style>
</head>
<body>

<section class="card card--front" aria-label="Business card front">
  <div class="wordmark">
    <span class="wordmark__name">TK VERDANE</span>
    <span class="wordmark__tag">CONSULTING LLC</span>
  </div>
</section>

<section class="card card--back" aria-label="Business card back">
  <div class="wordmark">
    <span class="wordmark__name">TK VERDANE</span>
    <span class="wordmark__tag">CONSULTING LLC</span>
  </div>

  <svg class="wave" viewBox="0 0 709 405" aria-hidden="true">
    <path class="wave__base" d="M0 318 Q354 450 709 318 L709 405 L0 405 Z"/>
    <path class="wave__swoosh" d="M26 320 Q354 430 683 320 Q354 444 26 320 Z"/>
  </svg>

  <div class="person">
    <p class="person__name"><span class="person__first">Delia</span> Pratt</p>
    <p class="person__role">President</p>
  </div>

  <div class="divider"></div>

  <ul class="contact">
    <li class="contact__item">
      <svg class="contact__icon" viewBox="0 0 16 16" aria-hidden="true">
        <path d="M3 2 L6 2 L7 5 L5.5 6.5 Q7 9.5 9.5 10.5 L11 9 L14 10 L14 13 Q8 14 4 10 Q1.5 6.5 3 2 Z"/>
        <path d="M10 2 Q13.5 3 14 6"/>
      </svg>
      703-555-0142
    </li>
    <li class="contact__item">
      <svg class="contact__icon" viewBox="0 0 16 16" aria-hidden="true">
        <rect x="1.5" y="5" width="13" height="9.5"/>
        <path d="M1.5 5 L8 10 L14.5 5"/>
        <path d="M4 5 L4 2 L12 2 L12 5"/>
      </svg>
      prattdq47@mailvessa.com
    </li>
  </ul>
</section>

</body>
</html>
```